High-end law practice specializing in closely held business succession planning and complex estates

Solo practitioner whose practice specializes in high-net worth, complex estate planning needs muliple versions of letterhead black and white, please. Letterhead should incorporate slogan, "Protecting your family business is my business," for one and "Complex Estate Planning"; third with no slogan. All for The Law Office of Marcy Lynn Pettibone, PC, 418 Cedar Hollow Ln., Newport News, Virginia 23648, Tel. 757-555-0142 Fax tbd email: marcy@mlplawgroup.example; Marcy Lynn Pettibone, Esq., principal, licensed in VA, NY, DC
Updates

Project Deadline Extended
Reason: My internet service went down and I can only view designs on my smart phone -- it's just too hard to review. So sorry! Working with my ISP now. Please be patient!

Target Market(s)

High net worth clients with complex estate planning needs, family businesses, family farmers, family foresters -- people with unique estate/succession planning needs who need a specialist who understands them.

Industry/Entity Type

Business

Font styles to use
Script

Requirements
Must have
• A high-end look and feel, connoting trustworthiness, special knowledge, and expertise.

```html
<!DOCTYPE html>
<html lang="en">
<head>
<meta charset="utf-8">
<title>Letterhead – The Law Office of Marcy Lynn Pettibone, PC</title>
<link rel="stylesheet" href="https://fonts.googleapis.com/css2?family=Arimo:wght@400;700&family=PT+Sans:wght@400;700&display=swap">
<style>
  :root {
    --backdrop: #e9e7e4;
    --paper: #ffffff;
    --ink: #000000;
    --ink-soft: #1a1a1a;
    --rule: #b5b5b5;
  }
  * { margin: 0; padding: 0; box-sizing: border-box; }
  html, body {
    width: 953px;
    height: 1200px;
    overflow: hidden;
    background: var(--backdrop);
  }
  .canvas {
    position: relative;
    width: 953px;
    height: 1200px;
  }
  .letterhead {
    position: absolute;
    left: 126px;
    top: 148px;
    width: 675px;
    height: 947px;
    background: var(--paper);
    box-shadow: 0 2px 10px rgba(0,0,0,0.12);
  }
  .firm {
    position: absolute;
    left: 31px;
    top: 36px;
    font-family: "Arimo", Arial, sans-serif;
    color: var(--ink);
  }
  .firm-name {
    font-weight: 700;
    font-size: 19.5px;
    line-height: 23px;
    letter-spacing: 0.1px;
    text-transform: uppercase;
  }
  .firm-principal {
    font-size: 13px;
    line-height: 16px;
    margin-top: 0;
  }
  .contact {
    position: absolute;
    left: 453px;
    top: 34px;
    padding-left: 9px;
    border-left: 1px solid var(--rule);
    font-family: "PT Sans", "Myriad Pro", sans-serif;
    font-size: 12.3px;
    line-height: 16.5px;
    color: var(--ink-soft);
  }
  .contact .address { margin-bottom: 3px; }
  .contact b { font-weight: 700; }
  .slogan {
    position: absolute;
    left: 0;
    right: 0;
    top: 910px;
    text-align: center;
    font-family: "Arimo", Arial, sans-serif;
    font-size: 15.5px;
    letter-spacing: 0.4px;
    color: var(--ink);
  }
</style>
</head>
<body>
<main class="canvas">
  <article class="letterhead">
    <header class="firm">
      <h1 class="firm-name">The Law Office<br>of Marcy Lynn Pettibone, PC</h1>
      <p class="firm-principal">Marcy Lynn Pettibone, Esq., licensed in VA, NY, DC</p>
    </header>
    <address class="contact">
      <div class="address">418 Cedar Hollow Ln.,<br>Newport News, Virginia 23648</div>
      <div><b>T</b>: 757-555-0142 | <b>F</b>: 757-555-0143</div>
      <div><b>E</b>: marcy@mlplawgroup.example</div>
    </address>
    <footer class="slogan">Complex Estate Planning</footer>
  </article>
</main>
</body>
</html>
```